Structural Engineering Business Card

Brookvane Drafting does residential house plans for clients in Central Florida. Would like simple but elegant business card that is appropriate for a house plan engineering company. Prefer black business card with black/white them but open to other shades of blue. I uploaded a sample card that I came across that looked good but please come up with your own creative designs.

Contact Information for Business Card

Name, Title, Phone, Email, Address, website

```html
<!DOCTYPE html>
<html lang="en">
<head>
<meta charset="utf-8">
<title>Brookvane Drafting – Business Card</title>
<link rel="stylesheet" href="https://fonts.googleapis.com/css2?family=Lexend:wght@600&family=Poppins:wght@400;700&display=swap">
<style>
  :root {
    --backdrop: #6b6b6b;
    --paper: #ffffff;
    --ink: #000000;
    --rule: #7a7a7a;
    --muted: #3a3a3a;
  }
  * { margin: 0; padding: 0; box-sizing: border-box; }
  html, body { width: 1093px; height: 1200px; overflow: hidden; }
  body { background: var(--backdrop); position: relative; font-family: "Poppins", sans-serif; }

  .card {
    position: absolute; left: 265px; width: 577px; height: 356px;
    border-radius: 24px; overflow: hidden;
  }
  .card--front { top: 226px; background: var(--paper); color: var(--ink); }
  .card--back { top: 621px; background: var(--ink); }

  .map-block {
    position: absolute; left: 290px; top: 0; width: 287px; height: 256px;
    background: var(--ink); border-bottom-left-radius: 60px;
  }
  .front-brand {
    position: absolute; left: 318px; top: 72px; width: 240px;
    color: var(--paper); font-weight: 700; font-size: 34px; line-height: 1.05;
  }

  .holder { position: absolute; left: 31px; top: 83px; }
  .holder__name { font-family: "Lexend", sans-serif; font-weight: 600; font-size: 21px; letter-spacing: 0.5px; line-height: 1; }
  .holder__title { font-size: 16px; color: var(--muted); margin-top: 2px; }

  .rule { position: absolute; left: 32px; width: 66px; height: 1.5px; background: var(--rule); }
  .rule--top { top: 152px; }
  .rule--bottom { top: 259px; }

  .contacts { position: absolute; left: 31px; top: 172px; list-style: none; font-size: 16.5px; line-height: 21px; }
  .contacts li { display: flex; align-items: center; gap: 7px; }
  .contacts svg { width: 15px; height: 15px; flex: none; }

  .address { position: absolute; left: 32px; top: 276px; font-size: 16.5px; line-height: 21px; }

  .back-brand {
    position: absolute; inset: 0; display: flex; align-items: center; justify-content: center;
    color: var(--paper); font-weight: 700; font-size: 40px; letter-spacing: 0.5px;
  }
</style>
</head>
<body>
  <section class="card card--front">
    <div class="map-block" role="img" aria-label="Large silhouette of the state of Florida"></div>
    <div class="front-brand">Brookvane<br>Drafting</div>

    <div class="holder">
      <div class="holder__name">MARLOW KEANE</div>
      <div class="holder__title">Managing Director</div>
    </div>
    <div class="rule rule--top"></div>

    <ul class="contacts">
      <li>
        <svg viewBox="0 0 24 24" aria-hidden="true"><path fill="currentColor" d="M6.6 10.8a15 15 0 0 0 6.6 6.6l2.2-2.2a1 1 0 0 1 1-.25 11.4 11.4 0 0 0 3.6.57 1 1 0 0 1 1 1V20a1 1 0 0 1-1 1A17 17 0 0 1 3 4a1 1 0 0 1 1-1h3.5a1 1 0 0 1 1 1c0 1.25.2 2.45.57 3.6a1 1 0 0 1-.25 1z"/></svg>
        044-555 018 274
      </li>
      <li>
        <svg viewBox="0 0 24 24" aria-hidden="true"><rect x="2" y="5" width="20" height="14" fill="currentColor"/><path d="M2 5l10 8 10-8" fill="none" stroke="#fff" stroke-width="1.6"/></svg>
        hello@brookvane.com
      </li>
      <li>
        <svg viewBox="0 0 24 24" aria-hidden="true"><g fill="none" stroke="currentColor" stroke-width="1.8"><circle cx="12" cy="12" r="10"/><ellipse cx="12" cy="12" rx="4.5" ry="10"/><path d="M2 12h20M4 7h16M4 17h16"/></g></svg>
        www.brookvane.com
      </li>
    </ul>
    <div class="rule rule--bottom"></div>

    <address class="address" style="font-style:normal">
      218, Cypress Hollow Lane<br>32801, Orlando FL
    </address>
  </section>

  <section class="card card--back">
    <div class="back-brand">Brookvane Drafting</div>
  </section>
</body>
</html>
```